Brightbay Orthodontics business card design

Need a business card design that reflects our re-branding (orthodontic office - braces) and a new partnership with a pediatric dental office. We would like to include "for adults and children" on the card as well so adults know they are welcome to get their braces here as well. Office design is modern and would like business card to reflect a modern type look. Here's the text we would like to be included on the card:

Darren Wolcott, DDS, MSD
5214 West Linden Avenue, Suite 204
Mansfield, TX 76991
555-418-2637
www.brightbayortho.example
info@brightbayortho.example

Can we add the following to the existing designs? Darren Wolcott, DDS, MSD 5214 West Linden Avenue, Suite 204 Mansfield, TX 76991 555-418-2637

Does anyone have any more vertical designs available? Thanks!

Dental

```html
<!DOCTYPE html>
<html lang="en">
<head>
<meta charset="UTF-8">
<title>Brightbay Orthodontics – Business Card</title>
<link href="https://fonts.googleapis.com/css2?family=Open+Sans:wght@400;600;700;800&display=swap" rel="stylesheet">
<style>
  :root {
    --stage: #2b2b2d;
    --card: #ffffff;
    --brand-blue: #1a78c2;
    --panel-blue: #1d7fcb;
    --ink: #1f1f1f;
    --muted: #8a8a8a;
    --accent-orange: #f7941d;
    --photo-warm: #efd6bc;
    --photo-pink: #f1b9c6;
    --photo-light: #f7ecdf;
  }
  * { box-sizing: border-box; margin: 0; padding: 0; }
  html, body { width: 1200px; height: 1000px; overflow: hidden; }
  body {
    background: var(--stage);
    font-family: "Open Sans", Arial, sans-serif;
    display: flex;
    align-items: center;
    justify-content: center;
    gap: 70px;
  }
  .card {
    position: relative;
    width: 340px;
    height: 595px;
    background: var(--card);
    border-radius: 16px;
    overflow: hidden;
    box-shadow: 0 14px 40px rgba(0,0,0,0.45);
  }

  /* Brand name block (stands in the logo position) */
  .brand {
    display: flex;
    align-items: center;
    gap: 12px;
    color: var(--ink);
    font-weight: 800;
    font-size: 29px;
    line-height: 1.05;
  }
  .brand-dot {
    width: 38px; height: 38px;
    border-radius: 50%;
    background: var(--brand-blue);
    flex: none;
  }

  /* Front card */
  .front .doctor {
    position: absolute;
    top: 70px; left: 0; right: 0;
    text-align: center;
  }
  .doctor-name {
    color: var(--brand-blue);
    font-weight: 700;
    font-size: 24px;
  }
  .doctor-credentials {
    color: var(--muted);
    font-weight: 700;
    font-size: 14px;
    margin-top: 2px;
  }
  .front .brand {
    position: absolute;
    top: 210px; left: 40px;
  }
  .contact-panel {
    position: absolute;
    left: 0; right: 0; bottom: 0;
    height: 250px;
    background: var(--panel-blue);
    border-radius: 14px 14px 0 0;
    padding: 34px 26px 0 30px;
    color: #ffffff;
  }
  .address { font-size: 15px; line-height: 1.4; }
  .phone {
    color: var(--accent-orange);
    font-weight: 700;
    font-size: 26px;
    margin-top: 18px;
  }
  .email { font-size: 15px; margin-top: 12px; }

  /* Back card */
  .back .brand {
    position: absolute;
    top: 60px; left: 50px;
  }
  .web-pill {
    position: absolute;
    top: 170px; left: 26px; right: 26px;
    height: 40px;
    border-radius: 20px;
    background: var(--panel-blue);
    color: #ffffff;
    font-size: 16px;
    letter-spacing: 0.5px;
    display: flex;
    align-items: center;
    justify-content: center;
  }
  .family-photo {
    position: absolute;
    left: 0; right: 0; bottom: 0;
    height: 345px;
    background: linear-gradient(135deg, var(--photo-light) 0%, var(--photo-warm) 45%, var(--photo-pink) 100%);
  }
</style>
</head>
<body>

  <article class="card front">
    <div class="doctor">
      <p class="doctor-name">Darren Wolcott</p>
      <p class="doctor-credentials">DDS, MSD</p>
    </div>
    <div class="brand">
      <span class="brand-dot"></span>
      <span>Brightbay<br>Orthodontics</span>
    </div>
    <div class="contact-panel">
      <p class="address">5214 West Linden Avenue, Suite 204<br>Mansfield, TX 76991</p>
      <p class="phone">555-418-2637</p>
      <p class="email">info@brightbayortho.example</p>
    </div>
  </article>

  <article class="card back">
    <div class="brand">
      <span class="brand-dot"></span>
      <span>Brightbay<br>Orthodontics</span>
    </div>
    <div class="web-pill">www.brightbayortho.example</div>
    <div class="family-photo" role="img" aria-label="Photo of a smiling mother hugging her young daughter"></div>
  </article>

</body>
</html>
```